Building company buisness cards

We are looking for a sharp modern new look for our business cards.We are a New Zealand based company that specialises in house and land packages.We have attached a photo of the current logo and would like to see if it can be improved somehow if needed.We are open to any colours but we have chosen Black and White at this stage. Feel free to change the font and make the logo smarter looking.Play with the colours and see what looks best.We want a card that looks so good know one will want to throw it away!

Target Market(s)

Building profesonals, home buyers

Industry/Entity Type

Building

Contact Information for Business Card

Garrick Tenwood
0275390628
garrickt@hartvale.co.nz

Font styles to use
Serif
Sans Serif

Colors

Designer to choose colors to be used in the design.

Requirements
Must have
• Just the logo on one side and details on the other
• Clean simple looking card
Nice to have
• Round corners and detail like raised or spot UV
• Something that stands out
Should not have
• To title needed, Director etc

```html
<!DOCTYPE html>
<html lang="en">
<head>
<meta charset="utf-8">
<title>Hartvale Business Card</title>
<link rel="stylesheet" href="https://fonts.googleapis.com/css2?family=Playfair+Display:wght@900&family=Montserrat:wght@400;500&display=swap">
<style>
  :root {
    --backdrop: #1c1c1c;
    --card: #121212;
    --ink: #ffffff;
    --silver: #cfcfcf;
    --rule: #6a6a6a;
  }
  * { margin: 0; padding: 0; box-sizing: border-box; }
  html, body {
    width: 1200px;
    height: 900px;
    overflow: hidden;
    background: var(--backdrop);
  }
  .stage {
    position: relative;
    width: 1200px;
    height: 900px;
  }
  .card {
    position: absolute;
    left: 350px;
    width: 500px;
    height: 300px;
    background: var(--card);
    border-radius: 22px;
    color: var(--ink);
  }
  .card--front { top: 110px; }
  .card--back { top: 480px; }

  .front-mark {
    position: absolute;
    inset: 0;
    display: flex;
    align-items: center;
    justify-content: center;
    gap: 16px;
  }
  .front-mark__name {
    font-family: "Playfair Display", Georgia, serif;
    font-weight: 900;
    font-size: 46px;
    color: var(--silver);
    letter-spacing: 0.5px;
  }
  .front-mark__ring { width: 52px; height: 52px; }

  .details {
    position: absolute;
    left: 80px;
    top: 58px;
    width: 360px;
  }
  .brand {
    display: flex;
    align-items: center;
    gap: 12px;
  }
  .brand__name {
    font-family: "Playfair Display", Georgia, serif;
    font-weight: 900;
    font-size: 58px;
    line-height: 1;
    color: var(--ink);
  }
  .brand__ring { width: 50px; height: 50px; }
  .tagline {
    font-family: "Montserrat", Arial, sans-serif;
    font-size: 13px;
    color: var(--ink);
    margin-top: 4px;
    letter-spacing: 0.3px;
  }
  .contact {
    margin-top: 18px;
    margin-left: 110px;
    width: 200px;
    text-align: center;
  }
  .contact__name {
    font-family: "Playfair Display", Georgia, serif;
    font-weight: 900;
    font-size: 21px;
    color: var(--ink);
  }
  .contact__rule {
    height: 1px;
    background: var(--rule);
    margin: 8px 0 10px;
  }
  .contact__line {
    font-family: "Montserrat", Arial, sans-serif;
    font-size: 14px;
    line-height: 1.5;
    color: var(--ink);
    white-space: nowrap;
  }
</style>
</head>
<body>
<main class="stage">
  <section class="card card--front" aria-label="Card front">
    <div class="front-mark">
      <span class="front-mark__name">Hartvale</span>
      <svg class="front-mark__ring" viewBox="0 0 52 52" aria-hidden="true">
        <circle cx="26" cy="26" r="23" fill="none" stroke="var(--silver)" stroke-width="3"/>
      </svg>
    </div>
  </section>

  <section class="card card--back" aria-label="Card back">
    <div class="details">
      <div class="brand">
        <span class="brand__name">Hartvale</span>
        <svg class="brand__ring" viewBox="0 0 50 50" aria-hidden="true">
          <circle cx="25" cy="25" r="22" fill="none" stroke="var(--ink)" stroke-width="3"/>
        </svg>
      </div>
      <p class="tagline">Houses shaped for life.</p>
      <div class="contact">
        <p class="contact__name">Garrick Tenwood</p>
        <div class="contact__rule"></div>
        <p class="contact__line">P: 0275390628</p>
        <p class="contact__line">E: garrickt@hartvale.co.nz</p>
      </div>
    </div>
  </section>
</main>
</body>
</html>
```